Harborline Renewal Business Card Design

Professional and clean design. The design colors should flow with the logo. Two-sided card with the website on the back which is:

www.HarborlineRenewal.example.

"Specializing in Water Damage Restoration"

On the front I need the name, email, phone, and logo.

Name: Darnell Quisby
Email: Darnell@HarborlineRenewal.example
Phone: 555-318-2046 for now

I only have the Preview and Thumbnail right now but should have the source files uploaded within a day or two.

Target Market(s)

Flood victims, home owners with water damage from busted pipes etc...

Industry/Entity Type

Business

Contact Information for Business Card

Name: Darnell Quisby

Font styles to use
Serif
Sans Serif

Requirements
Must have
• Business Card Details Info

```html
<!DOCTYPE html>
<html lang="en">
<head>
<meta charset="UTF-8">
<title>Harborline Renewal — Business Card</title>
<link href="https://fonts.googleapis.com/css2?family=Cinzel:wght@400;700&family=Open+Sans:wght@400;600&display=swap" rel="stylesheet">
<style>
  :root {
    --page: #e6e4e1;
    --card-dark: #0d0d0e;
    --card-mid: #1e1f21;
    --card-edge: #2a2b2d;
    --brand-blue: #2f9bd9;
    --brand-light: #5bbcef;
    --ink-white: #f2f2f2;
    --rule: #6b6b6b;
  }
  * { box-sizing: border-box; margin: 0; padding: 0; }
  html, body {
    width: 1200px; height: 1120px; overflow: hidden;
    background: var(--page);
  }
  .sheet {
    width: 1200px; height: 1120px;
    display: flex; flex-direction: column; align-items: center;
    gap: 40px; padding-top: 20px;
  }
  .card {
    position: relative;
    width: 960px; height: 520px;
    border-radius: 6px;
    background:
      linear-gradient(90deg, rgba(255,255,255,0.03), rgba(0,0,0,0.2) 30%, rgba(255,255,255,0.04) 55%, rgba(0,0,0,0.25) 80%, rgba(255,255,255,0.03)),
      radial-gradient(ellipse at 50% 30%, var(--card-mid), var(--card-dark) 75%);
    box-shadow: 0 10px 24px rgba(0,0,0,0.25);
    color: var(--ink-white);
    overflow: hidden;
  }
  .brand-dot {
    position: absolute; left: 50%; top: 54px;
    width: 104px; height: 104px; margin-left: -52px;
    border-radius: 50%;
    background: var(--brand-light);
  }
  .brand-name {
    position: absolute; left: 0; right: 0; top: 188px;
    text-align: center;
    font-family: "Cinzel", serif; font-weight: 700;
    font-size: 54px; letter-spacing: 2px;
    color: var(--brand-blue);
  }
  .tagline {
    position: absolute; left: 0; right: 0; top: 330px;
    text-align: center;
    font-family: "Cinzel", serif; font-weight: 400;
    font-size: 31px; letter-spacing: 1px;
    color: var(--ink-white);
  }
  .card--front .brand-dot { top: 40px; }
  .card--front .brand-name { top: 168px; }
  .contact-block {
    position: absolute; top: 310px; left: 0; right: 0;
    display: flex; justify-content: center; align-items: stretch; gap: 28px;
  }
  .person {
    text-align: right;
    padding-top: 16px;
  }
  .person-name, .person-title {
    font-family: "Cinzel", serif; font-weight: 700;
    font-size: 26px; line-height: 1.05; letter-spacing: 1px;
    color: var(--brand-blue);
  }
  .person-title { font-weight: 400; }
  .person-address {
    margin-top: 10px;
    font-family: "Open Sans", sans-serif; font-size: 20px; line-height: 1.35;
    color: var(--ink-white);
  }
  .divider { width: 2px; background: var(--rule); }
  .contact-list { list-style: none; padding-top: 4px; }
  .contact-list li {
    display: flex; align-items: center; gap: 12px;
    font-family: "Open Sans", sans-serif; font-size: 20px; line-height: 1.9;
    color: var(--ink-white);
  }
  .contact-list svg { width: 18px; height: 18px; flex: none; }
</style>
</head>
<body>
<main class="sheet">

  <section class="card card--back" aria-label="Card back">
    <div class="brand-dot"></div>
    <h1 class="brand-name">Harborline Renewal</h1>
    <p class="tagline">Specializing in Water Damage Restoration</p>
  </section>

  <section class="card card--front" aria-label="Card front">
    <div class="brand-dot"></div>
    <h2 class="brand-name">Harborline Renewal</h2>
    <div class="contact-block">
      <div class="person">
        <p class="person-name">Darnell Quisby</p>
        <p class="person-title">Title</p>
        <p class="person-address">Street Name, City Name<br>Zipcode-12345</p>
      </div>
      <div class="divider"></div>
      <ul class="contact-list">
        <li>
          <svg viewBox="0 0 24 24" aria-hidden="true"><circle cx="12" cy="12" r="11" fill="none" stroke="var(--brand-light)" stroke-width="2"/><path d="M8 6.5l2 0 1 3-1.5 1a7 7 0 0 0 4 4l1-1.5 3 1v2a1.5 1.5 0 0 1-1.5 1.5A10 10 0 0 1 6.5 8 1.5 1.5 0 0 1 8 6.5z" fill="var(--brand-light)"/></svg>
          555-318-2046
        </li>
        <li>
          <svg viewBox="0 0 24 24" aria-hidden="true"><circle cx="12" cy="12" r="11" fill="var(--brand-light)"/><rect x="6" y="8" width="12" height="8" fill="var(--card-dark)"/><path d="M6 8l6 5 6-5" fill="none" stroke="var(--brand-light)" stroke-width="1.5"/></svg>
          Darnell@HarborlineRenewal.example
        </li>
        <li>
          <svg viewBox="0 0 24 24" aria-hidden="true"><circle cx="12" cy="12" r="10" fill="none" stroke="var(--brand-light)" stroke-width="2"/><ellipse cx="12" cy="12" rx="4" ry="10" fill="none" stroke="var(--brand-light)" stroke-width="1.5"/><path d="M2 12h20M4 7h16M4 17h16" stroke="var(--brand-light)" stroke-width="1.5"/></svg>
          www.HarborlineRenewal.example
        </li>
      </ul>
    </div>
  </section>

</main>
</body>
</html>
```